Dermal Care Nursing Circle - Rack Card Design

This is a 2-sided rack card that should be 3.5 inches wide by 8.5 inches tall.

Text (with instructions), logo and website image are attached. For the main image on the front, you can use the attached image, or pull whatever you like off of pictovault.example, and we will purchase the photo from the winning design

The front should have text plus a nurse image, the back should have mostly text with the website image and legend.
Updates

We have received many high quality designs, but it is apparent to us that at the print size we are currently using (3.5x8.5), that the image of the homepage on the back is too small, and not legible. As such, we have decided that we would like to go with a horizontal version at 8.5 wide by 5.5 tall, with a larger more legible version of the website on the back and call outs to one side or the other, please resubmit your designs in that format. Thank you, and sorry for the inconvenience. Ned

Industry/Entity Type

Nurse

Font styles to use
Sans Serif

Colors
876aae
6b449b
b7a5cd
e4daeb

Requirements
Must have
• Please use the color palate from the attached logo, and a nursing image on the front.

```html
<!DOCTYPE html>
<html lang="en">
<head>
<meta charset="utf-8">
<title>Dermal Care Nursing Circle – Rack Card</title>
<link href="https://fonts.googleapis.com/css2?family=Catamaran:wght@600;700;800&family=Lato:wght@400;700&display=swap" rel="stylesheet">
<style>
  :root {
    --purple-deep: #5b3a8c;
    --purple: #6b449b;
    --purple-mid: #876aae;
    --purple-soft: #b7a5cd;
    --lavender: #e4daeb;
    --ink: #222228;
    --grey-text: #444;
    --stage: #ebe8ef;
  }
  * { box-sizing: border-box; margin: 0; padding: 0; }
  html, body { width: 1200px; height: 1200px; overflow: hidden; }
  body {
    background: var(--stage);
    font-family: "Lato", sans-serif;
    position: relative;
  }
  .rack-card {
    position: absolute;
    top: 36px;
    width: 466px;
    height: 1127px;
    overflow: hidden;
    background: linear-gradient(180deg, #ece7f3 0%, #f6f5f8 55%, #ffffff 100%);
    box-shadow: 0 4px 14px rgba(0,0,0,.18);
  }
  .rack-card--front { left: 113px; }
  .rack-card--back { left: 621px; }
  .layer { position: absolute; inset: 0; width: 466px; height: 1127px; }

  /* front typography */
  .tagline {
    position: absolute; left: 0; right: 0; top: 748px;
    text-align: center; font-family: "Catamaran", sans-serif;
  }
  .tagline__line--accent { color: var(--purple); font-weight: 800; font-size: 40px; line-height: 1; }
  .tagline__line--caps { color: #333; font-weight: 700; font-size: 27px; letter-spacing: .5px; line-height: 1; margin: 12px 0 10px; }

  /* lockup */
  .lockup {
    position: absolute; left: 0; right: 0;
    display: flex; flex-direction: column; align-items: center; gap: 8px;
    font-family: "Catamaran", sans-serif;
  }
  .rack-card--front .lockup { top: 935px; }
  .rack-card--back .lockup { top: 955px; }
  .lockup__main { display: flex; align-items: center; gap: 10px; }
  .lockup__dot { width: 16px; height: 16px; border-radius: 50%; background: var(--ink); flex: none; }
  .lockup__name { color: var(--purple); font-weight: 700; font-size: 30px; line-height: 1; }
  .lockup__org { color: var(--purple); font-weight: 600; font-size: 14px; letter-spacing: 3px; text-transform: uppercase; }

  .footer-url {
    position: absolute; left: 50px; top: 1083px;
    color: #fff; font-size: 17px; letter-spacing: .3px;
  }

  /* back typography */
  .back-intro {
    position: absolute; left: 20px; right: 20px; top: 345px;
    text-align: center; font-family: "Lato", sans-serif; font-weight: 700;
    color: var(--ink); font-size: 20.5px; line-height: 29px;
  }
  .back-intro__url {
    display: block; color: var(--purple); letter-spacing: 2.5px; margin-top: 2px; font-size: 20px;
  }
  .benefits { position: absolute; left: 32px; right: 34px; top: 490px; list-style: none; }
  .benefits__item {
    display: flex; gap: 10px; margin-bottom: 15px;
    font-size: 16px; line-height: 20px; color: var(--ink);
  }
  .benefits__badge {
    flex: none; width: 26px; height: 26px; border-radius: 50%;
    border: 2px solid var(--purple); background: #fff;
    color: var(--purple); font-weight: 700; font-size: 14px;
    display: flex; align-items: center; justify-content: center; margin-top: -2px;
  }
  .benefits__text { text-align: justify; }
</style>
</head>
<body>

<!-- FRONT -->
<section class="rack-card rack-card--front">
  <svg class="layer" viewBox="0 0 466 1127" role="img" aria-label="Smiling nurse in blue scrubs with a stethoscope, arms crossed, colleague blurred behind">
    <defs>
      <linearGradient id="frontPhoto" x1="0" y1="0" x2="1" y2="1">
        <stop offset="0" stop-color="#d9d2e8"/>
        <stop offset=".45" stop-color="#9aa3d6"/>
        <stop offset="1" stop-color="#6c74b3"/>
      </linearGradient>
    </defs>
    <path d="M0 0 H466 V400 C330 540 150 620 0 680 Z" fill="url(#frontPhoto)"/>
  </svg>
  <svg class="layer" viewBox="0 0 466 1127" aria-hidden="true">
    <defs>
      <linearGradient id="greyBand" x1="0" y1="1" x2="1" y2="0">
        <stop offset="0" stop-color="#7d7d80"/>
        <stop offset=".6" stop-color="#b9b9bc"/>
        <stop offset="1" stop-color="#8c8c90"/>
      </linearGradient>
    </defs>
    <path d="M0 680 C150 620 330 540 466 400 V440 C330 570 150 650 0 705 Z" fill="#6b449b"/>
    <path d="M0 705 C150 650 330 570 466 440 V560 C340 600 160 670 0 760 Z" fill="url(#greyBand)"/>
    <path d="M320 598 C390 615 440 650 466 690" fill="none" stroke="#6b449b" stroke-width="8"/>
    <path d="M230 1068 C340 1050 420 1020 466 990 V1015 C420 1040 350 1062 300 1068 Z" fill="#6b449b"/>
    <rect x="0" y="1065" width="466" height="62" fill="#5b3a8c"/>
    <path d="M290 1127 C360 1100 420 1070 466 1035 V1127 Z" fill="#8c8c90"/>
  </svg>

  <div class="tagline">
    <p class="tagline__line--accent">Inspired by patients</p>
    <p class="tagline__line--caps">EMPOWERED BY KNOWLEDGE</p>
    <p class="tagline__line--accent">Impacting melanoma</p>
  </div>

  <div class="lockup">
    <div class="lockup__main"><span class="lockup__dot"></span><span class="lockup__name">Dermal Care Nursing Circle</span></div>
    <span class="lockup__org">Skin Forward Foundation</span>
  </div>

  <p class="footer-url">www.DermalCareCircle.org</p>
</section>

<!-- BACK -->
<section class="rack-card rack-card--back">
  <svg class="layer" viewBox="0 0 466 1127" role="img" aria-label="Four smiling nurses in navy scrubs standing with arms crossed outside a hospital">
    <defs>
      <linearGradient id="backPhoto" x1="0" y1="0" x2="1" y2="1">
        <stop offset="0" stop-color="#c9a98f"/>
        <stop offset=".45" stop-color="#3e4f8f"/>
        <stop offset="1" stop-color="#2f3f7c"/>
      </linearGradient>
    </defs>
    <path d="M0 0 H466 V272 C330 268 180 290 0 330 Z" fill="url(#backPhoto)"/>
  </svg>
  <svg class="layer" viewBox="0 0 466 1127" aria-hidden="true">
    <path d="M0 325 C180 285 330 262 466 268 V320 C330 290 180 300 0 345 Z" fill="#876aae"/>
    <path d="M0 330 C180 292 330 272 466 280 V300 C330 285 180 305 0 340 Z" fill="#6b449b"/>
    <path d="M230 1068 C340 1050 420 1020 466 990 V1015 C420 1040 350 1062 300 1068 Z" fill="#6b449b"/>
    <rect x="0" y="1065" width="466" height="62" fill="#5b3a8c"/>
    <path d="M290 1127 C360 1100 420 1070 466 1035 V1127 Z" fill="#5a5a5e"/>
  </svg>

  <p class="back-intro">
    You wear many hats and take care of patients with many different tumor types.<br>
    Check out for free access to:
    <span class="back-intro__url">www.DermalCareCircle.org</span>
  </p>

  <ul class="benefits">
    <li class="benefits__item"><span class="benefits__badge">A</span><span class="benefits__text">Hot off the press! Articles from the Journal of Practical Care Nursing outlining practical strategies to manage side-effects and promote adherence to melanoma therapies</span></li>
    <li class="benefits__item"><span class="benefits__badge">B</span><span class="benefits__text">Visual and text-based therapeutic side effect management tools</span></li>
    <li class="benefits__item"><span class="benefits__badge">C</span><span class="benefits__text">A Nurse’s Toolkit with extensive melanoma nursing care resources</span></li>
    <li class="benefits__item"><span class="benefits__badge">D</span><span class="benefits__text">Printable patient resources to provide patients, organized by therapy</span></li>
    <li class="benefits__item"><span class="benefits__badge">E</span><span class="benefits__text">An oncology nurse community forum to share successes, challenges, insights, and solutions</span></li>
    <li class="benefits__item"><span class="benefits__badge">F</span><span class="benefits__text">Online educational modules, newsfeeds, and other material to keep you up to date</span></li>
    <li class="benefits__item"><span class="benefits__badge">G</span><span class="benefits__text">And much more!</span></li>
  </ul>

  <div class="lockup">
    <div class="lockup__main"><span class="lockup__dot"></span><span class="lockup__name">Dermal Care Nursing Circle</span></div>
    <span class="lockup__org">Skin Forward Foundation</span>
  </div>

  <p class="footer-url">www.DermalCareCircle.org</p>
</section>

</body>
</html>
```